Real Estate Wordpress Landing Page

I'm looking to a landing page dedicated to my real estate brokerage that's catered to promoting that my company provides 1.5% listings to home sellers... I have a couple examples that I'm really looking towards mocking in a version with similar color schemes using my current company colors/website.

http://harbelo.com/
https://www.quarvantis.com/about/one-percent-listing-fee

My brokerage company website is http://www.brightmarrow.us/

Target Market(s)

real estate home sellers & buyers

Industry/Entity Type

Real Estate

Coding

Coded - Design and coding required

Number of Pages Required

1 page

Colors
3176b5
0255a3
eaf1f7
cedeed

Requirements
Must have
• Company website colors - http://www.brightmarrow.us/
• Something around the lines of this website page - http://harbelo.com/
• Wordpress compatibility

```html
<!DOCTYPE html>
<html lang="en">
<head>
<meta charset="utf-8">
<title>Bright Marrow Realty – List for 1.5% Commission</title>
<link rel="stylesheet" href="https://fonts.googleapis.com/css2?family=Roboto+Condensed:wght@400;700&family=Roboto:wght@400;500&display=swap">
<style>
:root{
  --blue:#3176b5;
  --blue-deep:#0255a3;
  --blue-pale:#eaf1f7;
  --blue-soft:#cedeed;
  --ink:#2b2b2b;
  --grey-text:#9a9a9a;
  --panel:#efefef;
  --band:#f5f5f5;
  --footer:#3d3935;
  --white:#ffffff;
}
*{box-sizing:border-box;margin:0;padding:0}
html,body{width:1200px;height:3255px;overflow:hidden}
body{position:relative;background:var(--white);font-family:"Roboto Condensed",Arial,sans-serif;color:var(--ink)}
.abs{position:absolute}

/* header */
.brand{left:52px;top:22px;display:flex;align-items:center;gap:12px;font-weight:700;font-size:26px;color:var(--blue-deep)}
.brand-mark{width:34px;height:34px;background:var(--blue-deep)}
.nav{right:52px;top:52px;display:flex;gap:40px;align-items:center;font-size:16px}
.nav-phone{color:var(--grey-text);display:flex;gap:10px;align-items:center}
.nav-buy{color:var(--blue-deep);font-weight:700}
.nav-sell{color:var(--grey-text)}

/* hero */
.hero-photo{left:37px;top:126px;width:1126px;height:692px;background:linear-gradient(180deg,#7e8a96 0%,#a7a59a 45%,#6f7a58 75%,#4f6a34 100%)}
.hero-title{left:70px;top:440px;font-size:72px;font-weight:700;color:var(--white);letter-spacing:1px}
.hero-sub{left:70px;top:536px;font-size:25px;color:var(--white)}
.btn-cases{left:70px;top:612px;width:245px;height:54px;background:var(--blue);color:var(--white);font-size:15px;font-weight:700;display:flex;align-items:center;justify-content:center}

.changing{left:67px;top:775px;width:534px;height:260px;background:var(--panel)}
.changing h2{position:absolute;left:82px;top:64px;font-size:80px;font-weight:700;color:#333;letter-spacing:1px}
.changing p{position:absolute;left:82px;top:170px;font-size:16px;color:var(--grey-text)}
.badge{left:561px;top:852px;width:80px;height:80px;border-radius:50%;background:var(--white);display:flex;align-items:center;justify-content:center}

.contact-form{left:601px;top:718px;width:534px;height:384px;background:var(--blue);padding:30px 78px 0}
.contact-form h3{font-size:20px;font-weight:700;color:var(--white);margin-bottom:18px}
.field{height:48px;background:var(--white);margin-bottom:8px;font-size:13px;color:var(--grey-text);padding:0 20px;display:flex;align-items:center;justify-content:space-between;width:400px}
.btn-save{margin-top:12px;width:356px;height:48px;border:2px solid var(--white);color:var(--white);font-size:15px;font-weight:700;display:flex;align-items:center;justify-content:center}

/* section heads */
.section-title{left:0;width:1200px;text-align:center;font-size:46px;font-weight:700;color:#222}
.section-title span{color:var(--blue-deep)}
.section-sub{left:0;width:1200px;text-align:center;font-size:22px;color:var(--grey-text)}

/* cards */
.card{top:1356px;width:343px;height:436px;background:var(--blue);overflow:hidden}
.card-photo{position:absolute;left:0;top:0;width:343px;height:240px}
.card-curve{position:absolute;left:0;top:0}
.card-body{position:absolute;left:26px;top:262px;color:var(--white)}
.saved{font-size:31px;font-weight:700;margin-bottom:22px}
.addr{font-size:14px;line-height:22px}
.more{margin-top:14px;font-size:14px;font-weight:700;display:flex;gap:8px;align-items:center}

.divider{left:52px;top:1892px;width:1096px;height:5px;border-top:1px solid var(--blue-soft);border-bottom:2px solid var(--blue-soft)}

/* feature */
.feature-photo{left:65px;top:2157px;width:534px;height:367px;background:linear-gradient(160deg,#cfd3d6 0%,#9aa0a4 50%,#e6e6e4 100%)}
.feature-panel{left:599px;top:2213px;width:536px;height:235px;background:var(--panel);padding:50px 38px;color:var(--blue-deep)}
.feature-panel .saved{font-size:31px;margin-bottom:18px}
.feature-panel .addr{color:#666}
.feature-panel .more{color:var(--blue-deep)}
.slide-btn{top:2474px;width:48px;height:48px;border:2px solid var(--blue-soft);background:var(--white);display:flex;align-items:center;justify-content:center}
.slide-prev{left:638px;border-color:var(--blue)}
.slide-next{left:688px;border-width:1px}

/* broker band */
.broker{left:0;top:2630px;width:1200px;height:289px;background:linear-gradient(180deg,var(--band) 0%,#ececec 100%)}
.broker h2{position:absolute;left:0;width:1200px;top:58px;text-align:center;font-size:34px;font-weight:700;color:#222}
.call-input{position:absolute;left:304px;top:152px;width:297px;height:52px;background:var(--white);font-size:14px;color:var(--grey-text);display:flex;align-items:center;justify-content:center}
.call-btn{position:absolute;left:601px;top:152px;width:306px;height:52px;background:var(--blue);color:var(--white);font-size:16px;font-weight:700;display:flex;align-items:center;justify-content:center;gap:12px}

/* footer */
.footer{left:0;top:2919px;width:1200px;height:336px;background:var(--footer);color:var(--white)}
.footer h4{position:absolute;left:102px;top:86px;font-size:20px;font-weight:700}
.footer-addr{position:absolute;left:102px;top:150px;font-family:Roboto,Arial,sans-serif;font-size:13px;line-height:23px}
.footer-brand{position:absolute;left:440px;top:140px;width:320px;display:flex;align-items:center;justify-content:center;gap:14px;font-size:34px;font-weight:700}
.footer-brand .brand-mark{background:var(--blue)}
.footer-contact{position:absolute;left:896px;top:110px;font-size:15px;font-weight:700;line-height:26px}
.footer-copy{position:absolute;left:896px;top:199px;font-family:Roboto,Arial,sans-serif;font-size:12px;color:#a9a39c}
</style>
</head>
<body>

<header>
  <div class="abs brand"><span class="brand-mark"></span>Bright Marrow Realty</div>
  <nav class="abs nav">
    <span class="nav-phone">
      <svg width="14" height="18" viewBox="0 0 14 18"><path d="M4 1 L1 2 C0 8 4 15 11 17 L13 14 L10 11 L8 12 C6 10 5 8 5 6 L7 5 Z" fill="var(--blue)"/></svg>
      555 - 201 - 4830</span>
    <span class="nav-buy">Buy with Us ▾</span>
    <span class="nav-sell">Sell with Us ▾</span>
  </nav>
</header>

<section class="hero">
  <div class="abs hero-photo" role="img" aria-label="Two-storey suburban house with front lawn and trees"></div>
  <h1 class="abs hero-title">LIST FOR 1.5% COMMISSION</h1>
  <p class="abs hero-sub">List for only 1.5% | Get 1% Back when you Purchase</p>
  <div class="abs btn-cases">View Cases</div>

  <div class="abs changing">
    <h2>CHANGING</h2>
    <p>The Way Real Estate is Sold and Purchased.</p>
  </div>
  <div class="abs badge">
    <svg width="46" height="40" viewBox="0 0 46 40"><path d="M4 22 L23 6 L42 22 M10 18 V36 H36 V18" fill="none" stroke="var(--blue)" stroke-width="4"/></svg>
  </div>

  <form class="abs contact-form">
    <h3>Talk To A Local Bright Marrow Agent</h3>
    <div class="field">Name :</div>
    <div class="field">Email :</div>
    <div class="field">Tel :</div>
    <div class="field">Select :<svg width="10" height="6"><path d="M0 0H10L5 6Z" fill="#333"/></svg></div>
    <div class="btn-save">CONTACT BRIGHT MARROW AND SAVE TODAY!</div>
  </form>
</section>

<section>
  <h2 class="abs section-title" style="top:1196px">List For 1.5% <span>Commission</span></h2>
  <p class="abs section-sub" style="top:1276px">And Receive Top Marketing from Real Estate Pro!</p>

  <article class="abs card" style="left:67px">
    <div class="card-photo" role="img" aria-label="Two-storey house with garage and palm trees" style="background:linear-gradient(180deg,#9dbbd3 0%,#d8d2bc 55%,#6f8f4a 100%)"></div>
    <svg class="card-curve" width="343" height="240"><path d="M0 210 C90 160 220 150 343 190 V240 H0 Z" fill="var(--blue)"/></svg>
    <div class="card-body"><div class="saved">Saved $4,650</div><div class="addr">2817 Willowmere Lane<br>Lakeshade, FL 33901 - $310,000</div><div class="more">Learn More →</div></div>
  </article>
  <article class="abs card" style="left:430px">
    <div class="card-photo" role="img" aria-label="Bright living room with sofa and ceiling fan" style="background:linear-gradient(180deg,#d9dcdf 0%,#8d9296 60%,#e5e5e3 100%)"></div>
    <svg class="card-curve" width="343" height="240"><path d="M0 210 C90 160 220 150 343 190 V240 H0 Z" fill="var(--blue)"/></svg>
    <div class="card-body"><div class="saved">Saved $7,485</div><div class="addr">914 Marisol Boulevard, 204<br>Fernwick, FL 33992 - $499,000</div><div class="more">Learn More →</div></div>
  </article>
  <article class="abs card" style="left:792px">
    <div class="card-photo" role="img" aria-label="Single-family home with palm trees and driveway" style="background:linear-gradient(180deg,#a6c3dc 0%,#e0d6b8 55%,#7a9452 100%)"></div>
    <svg class="card-curve" width="343" height="240"><path d="M0 210 C90 160 220 150 343 190 V240 H0 Z" fill="var(--blue)"/></svg>
    <div class="card-body"><div class="saved">Saved $4,650</div><div class="addr">7725 Old Stablegate Circle<br>Lakeshade, FL 33904 - $310,000</div><div class="more">Learn More →</div></div>
  </article>
</section>

<div class="abs divider"></div>

<section>
  <h2 class="abs section-title" style="top:1994px">30 Day Listing Service <span>Guaranteed.</span></h2>
  <p class="abs section-sub" style="top:2078px">Save thousands $$$ listing with us!Morbi eu sem felis. Integer faucibus ligula vitae enim vestibulum iaculis.</p>

  <div class="abs feature-photo" role="img" aria-label="Condo living room with sofa, ceiling fan and balcony view"></div>
  <div class="abs feature-panel">
    <div class="saved">Saved $4,200</div>
    <div class="addr">318 n Fairway Glen drive palmoria,<br>FL33918-$550,000</div>
    <div class="more">Learn More →</div>
  </div>
  <div class="abs slide-btn slide-prev"><svg width="8" height="10"><path d="M8 0V10L0 5Z" fill="var(--blue)"/></svg></div>
  <div class="abs slide-btn slide-next"><svg width="8" height="10"><path d="M0 0V10L8 5Z" fill="var(--blue-soft)"/></svg></div>
</section>

<section class="abs broker" role="img" aria-label="Faint city skyline backdrop">
  <h2>TEODOR VALCOURT, Lic. Real Estate Broker</h2>
  <div class="call-input">Call Us Today And Save Thousand $$$</div>
  <div class="call-btn">
    <svg width="14" height="18" viewBox="0 0 14 18"><path d="M4 1 L1 2 C0 8 4 15 11 17 L13 14 L10 11 L8 12 C6 10 5 8 5 6 L7 5 Z" fill="#fff"/></svg>
    555-208-3371</div>
</section>

<footer class="abs footer">
  <h4>Contact Us</h4>
  <p class="footer-addr">4200 Harbor Loop,<br>Ste 310, Fernwick,<br>FL 33990</p>
  <div class="footer-brand"><span class="brand-mark"></span>Bright Marrow</div>
  <p class="footer-contact">contact@brightmarrow.us<br>555-201-4830</p>
  <p class="footer-copy">© 2018 Bright Marrow, All right Reserved.</p>
</footer>

</body>
</html>
```